Brivora Distance Learning Website

Brivora provide e-learning and mixed learning solutions for individuals, colleges, organisations and B2B.
We need a modern, light and flat website design for Brivora. We want to to see the designer incorporate user experience(UX) design elements into the AI or PSD mockups. We would like to see designs that use pastel colors that compliment yellow and black of our logo.
We want our E-learning experience to accelerate learning and for the interface to be user friendly and intuitive. We want the designs to focus on quick access to course information, course reviews, learning progress and study advice. Quick and intuitive access to all content for our clients is one of our top priorities.
We would like designs for the following project 3 pages:
1. Learner homepage dashboard (see attached screenshot).
On this page the Learners need to:
- Login
- Have quick access to Packages and Courses.
- See other recommended courses (Below Packages and Courses)
- Possibly a left hand side column/menu with thumbnail icons (See lumeqa learner dashboard screenshot)
2. Homepage
See current sample
http://www.brivora-learn.example
We would like the designer to focus on creating a customized banner to enhance the home page.
3. Primary Landing/Marketing page
This page is geared towards customer acquisition with the focal point being the top banner (video or HD image).
And Course Preview content below.
See reference
http://brivora-learn.example/subscriptionPlans/marketing/MTc%3D/Mjc4Nw%3D%3D/Speaking%20Nepali%20%2B%20Nepali%20Snacks%20Bundle%20by%20Lorne%20Pike%20Vell
Other site we like:
- https://www.skillorva.example (We like the home page and top bar on courses page)
- http://www.tutorcrest.example
- http://pixelgrovelab.example (think this site looks great, love the lower graphics on the homepage)
Updates
Hello,
Thank you for taking the time to contribute to this web design competition. We would just like to point out a few things:
1. Please try to make the color palette similar to the colors used in the screenshot that we just uploaded ('possible color palette).
2. Please make the designs specific to each page: THE LEARNER HOMEPAGE, HOME PAGE, and the MARKETING LANDING PAGE.
We are very happy with the high quality of designs so far,
Cheers,
Ned Ru
VK-Studio
Also,
Please avoid using dark/bold elements in the designs. The ONLY elements that we want to be dark are the logo and the footer.
Any questions please ask,
Cheers,
Ned Ru
Vk-Studio
Hello,
Based on the round of feedback we just gave it would be great if you could complete further design changes by tomorrow, as we are pushed for time.
Thank you,
Ned Ru
VK-Studio

```html
<!DOCTYPE html>
<html lang="en">
<head>
<meta charset="utf-8">
<title>Brivora – Learning Packages</title>
<link href="https://fonts.googleapis.com/css2?family=Open+Sans:wght@400;700&family=Raleway:wght@400;500&family=Roboto:wght@400;500;700&display=swap" rel="stylesheet">
<style>
:root{
  --yellow:#f6b923;
  --yellow-soft:#f9c23a;
  --header-grey:#8f8f8f;
  --ink:#2f2f2f;
  --text:#333;
  --muted:#777;
  --page:#ebebeb;
  --field:#ececec;
  --line:#b9b9b9;
  --btn-top:#8a8a8a;
  --btn-bottom:#5f5f5f;
  --white:#fff;
}
*{box-sizing:border-box;margin:0;padding:0}
html,body{width:1080px;height:1200px;overflow:hidden}
body{position:relative;background:var(--page);font-family:"Roboto",sans-serif;color:var(--text)}

/* header */
.site-header{position:absolute;left:0;top:0;width:1080px;height:84px;background:var(--header-grey)}
.brand{position:absolute;left:88px;top:20px;display:flex;align-items:center;gap:8px}
.brand-dot{width:34px;height:34px;border-radius:50%;background:var(--yellow)}
.brand-name{font-family:"Raleway",sans-serif;font-weight:500;font-size:32px;color:var(--white);line-height:1}
.top-links{position:absolute;top:10px;font-size:11px;color:var(--white)}
.lang{left:854px}
.lang::after{content:"";display:inline-block;width:4px;height:4px;border-right:1px solid #fff;border-bottom:1px solid #fff;transform:rotate(45deg);margin-left:10px;position:relative;top:-3px}
.signin{left:963px}
.search{position:absolute;left:528px;top:34px;display:flex}
.search-field{width:356px;height:28px;background:var(--white);font-size:11px;color:#555;padding:7px 11px}
.search-btn{width:112px;height:28px;background:var(--yellow);color:var(--ink);font-size:18px;text-align:center;line-height:28px}

/* hero */
.hero{position:absolute;left:0;top:84px;width:1080px;height:532px;overflow:hidden}
.hero-photo{position:absolute;inset:0;background:
  radial-gradient(ellipse at 62% 25%,#c98c68 0%,rgba(201,140,104,0) 35%),
  radial-gradient(ellipse at 85% 70%,#d7c6b2 0%,rgba(215,198,178,0) 45%),
  linear-gradient(100deg,#8d857a 0%,#d9d2c6 30%,#cbbba8 60%,#e2ddd2 100%)}
.hero-title{position:absolute;left:0;width:1080px;text-align:center;font-family:"Open Sans",sans-serif;font-weight:700;color:#3b3b3b;line-height:1}
.hero-title.one{top:92px;font-size:50px}
.hero-title.two{top:152px;font-size:50px}
.hero-sub{position:absolute;left:0;top:221px;width:1080px;text-align:center;font-family:"Raleway",sans-serif;font-size:18px;color:#1f1f1f}
.beta{position:absolute;left:273px;top:271px;width:527px;height:244px;background:var(--yellow-soft);border-radius:6px}
.beta h2{position:absolute;left:0;top:18px;width:527px;text-align:center;font-family:"Raleway",sans-serif;font-weight:500;font-size:28px;color:#1c1c1c}
.field{position:absolute;left:132px;width:276px;background:var(--field);font-size:12px;color:#9a9a9a;padding:8px 9px}
.field.email{top:70px;height:29px}
.field.reason{top:111px;height:61px;padding-top:9px}
.beta-btn{position:absolute;left:133px;top:188px;width:273px;height:35px;border-radius:3px;background:linear-gradient(var(--btn-top),var(--btn-bottom));color:#fff;font-size:15px;text-align:center;line-height:35px}

/* packages */
.section-title{position:absolute;left:83px;top:641px;font-family:"Raleway",sans-serif;font-weight:400;font-size:29px;color:#2b2b2b}
.section-rule{position:absolute;left:83px;top:685px;width:914px;height:1px;background:var(--line)}
.section-rule-strong{position:absolute;left:83px;top:684px;width:247px;height:2px;background:#8c8c8c}

.categories{position:absolute;left:83px;top:713px;width:202px;height:377px;background:var(--white);border:1px solid #ddd}
.cat-head{position:absolute;left:0;top:0;width:200px;height:33px;background:linear-gradient(#f7c02f,#f0ae12);font-family:"Raleway",sans-serif;font-weight:400;font-size:19px;color:#222;text-align:center;line-height:36px}
.cat-notch{position:absolute;left:88px;top:33px}
.cat-list{position:absolute;left:5px;top:64px;width:192px;list-style:none}
.cat-list li{height:30px;line-height:30px;font-size:11px;color:#222;padding-left:17px;position:relative}
.cat-list li::before{content:"";position:absolute;left:6px;top:13px;border-left:3px solid #333;border-top:2px solid transparent;border-bottom:2px solid transparent}
.cat-list li.active{background:#e9e9e9}

.card{position:absolute;top:713px;width:185px;height:335px;background:#f7f7f7;border:1px solid #cfcfcf;border-radius:3px;box-shadow:0 1px 2px rgba(0,0,0,.12)}
.card-art{position:absolute;left:9px;top:9px;width:165px;height:142px;background:linear-gradient(#f7c12c,#f3b51c)}
.card-meta{position:absolute;left:0;top:158px;width:183px;height:37px;background:#e6e6e6;border-top:1px solid #c9c9c9;border-bottom:1px solid #c9c9c9;display:flex}
.meta-cat{width:89px;border-right:1px solid #c9c9c9;font-size:11px;line-height:13px;padding:6px 0 0 18px;color:#222}
.meta-views{flex:1;text-align:center;font-size:11px;font-weight:700;color:#222;padding-top:3px}
.meta-views svg{display:block;margin:0 auto 2px}
.reviews-label{position:absolute;left:0;top:204px;width:183px;text-align:center;font-size:11px;color:#222}
.stars{position:absolute;left:56px;top:218px;display:flex;gap:2px}
.course-name{position:absolute;left:14px;top:243px;width:160px;font-size:11px;line-height:13px;color:#222}
.course-by{position:absolute;left:14px;top:271px;font-size:11px;color:#222}
.course-by span{font-size:9px;color:var(--muted)}
.card-btn{position:absolute;left:12px;top:297px;width:157px;height:28px;border-radius:3px;background:linear-gradient(var(--btn-top),var(--btn-bottom));color:#fff;font-size:10px;font-weight:700;letter-spacing:.3px;display:flex;align-items:center;justify-content:center;gap:6px}

/* footer */
.site-footer{position:absolute;left:0;top:1114px;width:1080px;height:86px;background:var(--yellow)}
.foot-links{position:absolute;left:91px;top:16px;font-size:11.5px;line-height:18.5px;color:#222}
.foot-brand{position:absolute;left:812px;top:22px;display:flex;align-items:center;gap:8px}
.foot-brand .brand-dot{background:#1c1c1c}
.foot-brand .brand-name{color:#1c1c1c}
</style>
</head>
<body>

<header class="site-header">
  <div class="brand"><span class="brand-dot"></span><span class="brand-name">Brivora</span></div>
  <div class="top-links lang">English(US)</div>
  <div class="top-links signin">Sign In</div>
  <div class="search">
    <div class="search-field">What Can We Help You Learn Today?</div>
    <div class="search-btn">Search</div>
  </div>
</header>

<section class="hero">
  <div class="hero-photo" role="img" aria-label="Soft-focus photo of a learner working at a laptop in a bright office"></div>
  <h1 class="hero-title one">Your Learning Journey</h1>
  <div class="hero-title two">STARTS HERE</div>
  <p class="hero-sub">facilitating elegant e-learning and mixed learning solutions</p>
  <div class="beta">
    <h2>Join Our Beta Limited Availability</h2>
    <div class="field email">Email Address</div>
    <div class="field reason">Reason for Interest</div>
    <div class="beta-btn">Join Beta</div>
  </div>
</section>

<h2 class="section-title">Learning Packages</h2>
<div class="section-rule"></div>
<div class="section-rule-strong"></div>

<aside class="categories">
  <div class="cat-head">All Categories</div>
  <svg class="cat-notch" width="26" height="18" viewBox="0 0 26 18"><path d="M0 0 Q13 4 13 18 Q13 4 26 0Z" fill="#f0ae12"/></svg>
  <ul class="cat-list">
    <li>Business and Finance</li>
    <li>Marketing</li>
    <li class="active">IT &amp; Software</li>
    <li>Lifestyle</li>
    <li>Personal Development</li>
    <li>Photography</li>
    <li>Health and Fitness</li>
    <li>Education and Teaching</li>
    <li>Music</li>
    <li>Hotels and Hospitality</li>
  </ul>
</aside>

<article class="card" style="left:355px">
  <div class="card-art" role="img" aria-label="Nepali Snacks course cover artwork"></div>
  <div class="card-meta">
    <div class="meta-cat">Language<br>and...</div>
    <div class="meta-views"><svg width="14" height="9" viewBox="0 0 14 9"><ellipse cx="7" cy="4.5" rx="6.3" ry="3.8" fill="none" stroke="#555" stroke-width="1.3"/><circle cx="7" cy="4.5" r="1.8" fill="#555"/></svg>Views 1417</div>
  </div>
  <div class="reviews-label">Reviews</div>
  <div class="stars">
    <svg width="70" height="12" viewBox="0 0 70 12"><g id="s1"><path d="M6 0.5l1.6 3.5 3.8.4-2.9 2.6.9 3.8L6 8.8 2.6 10.8l.9-3.8L.6 4.4l3.8-.4z" fill="#f5b800" stroke="#b07d00" stroke-width=".6"/></g><use href="#s1" x="14"/><use href="#s1" x="28"/><use href="#s1" x="42"/><path transform="translate(56 0)" d="M6 0.5l1.6 3.5 3.8.4-2.9 2.6.9 3.8L6 8.8 2.6 10.8l.9-3.8L.6 4.4l3.8-.4z" fill="#aaa"/></svg>
  </div>
  <p class="course-name">Speaking Nepali Fundamentals Suite by Lorne Pike Vell</p>
  <p class="course-by">by <span>Lorne Vell</span></p>
  <div class="card-btn"><svg width="18" height="7" viewBox="0 0 18 7"><rect width="6" height="7" fill="#fff"/><rect x="8" y="0" width="10" height="1.4" fill="#fff"/><rect x="8" y="2.8" width="10" height="1.4" fill="#fff"/><rect x="8" y="5.6" width="10" height="1.4" fill="#fff"/></svg>DETAILS</div>
</article>

<article class="card" style="left:579px">
  <div class="card-art" role="img" aria-label="Nepali Snacks course cover artwork"></div>
  <div class="card-meta">
    <div class="meta-cat">Language<br>and...</div>
    <div class="meta-views"><svg width="14" height="9" viewBox="0 0 14 9"><ellipse cx="7" cy="4.5" rx="6.3" ry="3.8" fill="none" stroke="#555" stroke-width="1.3"/><circle cx="7" cy="4.5" r="1.8" fill="#555"/></svg>Views 1417</div>
  </div>
  <div class="reviews-label">Reviews</div>
  <div class="stars">
    <svg width="70" height="12" viewBox="0 0 70 12"><g id="s2"><path d="M6 0.5l1.6 3.5 3.8.4-2.9 2.6.9 3.8L6 8.8 2.6 10.8l.9-3.8L.6 4.4l3.8-.4z" fill="#f5b800" stroke="#b07d00" stroke-width=".6"/></g><use href="#s2" x="14"/><use href="#s2" x="28"/><use href="#s2" x="42"/><path transform="translate(56 0)" d="M6 0.5l1.6 3.5 3.8.4-2.9 2.6.9 3.8L6 8.8 2.6 10.8l.9-3.8L.6 4.4l3.8-.4z" fill="#aaa"/></svg>
  </div>
  <p class="course-name">Speaking Nepali Fundamentals Suite by Lorne Pike Vell</p>
  <p class="course-by">by <span>Lorne Vell</span></p>
  <div class="card-btn"><svg width="18" height="7" viewBox="0 0 18 7"><rect width="6" height="7" fill="#fff"/><rect x="8" y="0" width="10" height="1.4" fill="#fff"/><rect x="8" y="2.8" width="10" height="1.4" fill="#fff"/><rect x="8" y="5.6" width="10" height="1.4" fill="#fff"/></svg>DETAILS</div>
</article>

<article class="card" style="left:809px">
  <div class="card-art" role="img" aria-label="Nepali Snacks course cover artwork"></div>
  <div class="card-meta">
    <div class="meta-cat">Language<br>and...</div>
    <div class="meta-views"><svg width="14" height="9" viewBox="0 0 14 9"><ellipse cx="7" cy="4.5" rx="6.3" ry="3.8" fill="none" stroke="#555" stroke-width="1.3"/><circle cx="7" cy="4.5" r="1.8" fill="#555"/></svg>Views 1417</div>
  </div>
  <div class="reviews-label">Reviews</div>
  <div class="stars">
    <svg width="70" height="12" viewBox="0 0 70 12"><g id="s3"><path d="M6 0.5l1.6 3.5 3.8.4-2.9 2.6.9 3.8L6 8.8 2.6 10.8l.9-3.8L.6 4.4l3.8-.4z" fill="#f5b800" stroke="#b07d00" stroke-width=".6"/></g><use href="#s3" x="14"/><use href="#s3" x="28"/><use href="#s3" x="42"/><path transform="translate(56 0)" d="M6 0.5l1.6 3.5 3.8.4-2.9 2.6.9 3.8L6 8.8 2.6 10.8l.9-3.8L.6 4.4l3.8-.4z" fill="#aaa"/></svg>
  </div>
  <p class="course-name">Speaking Nepali Fundamentals Suite by Lorne Pike Vell</p>
  <p class="course-by">by <span>Lorne Vell</span></p>
  <div class="card-btn"><svg width="18" height="7" viewBox="0 0 18 7"><rect width="6" height="7" fill="#fff"/><rect x="8" y="0" width="10" height="1.4" fill="#fff"/><rect x="8" y="2.8" width="10" height="1.4" fill="#fff"/><rect x="8" y="5.6" width="10" height="1.4" fill="#fff"/></svg>DETAILS</div>
</article>

<footer class="site-footer">
  <div class="foot-links">
    <p>Copyright © 2015 Brivora.com</p>
    <p>Terms of Use</p>
    <p>Privacy Policy</p>
  </div>
  <div class="foot-brand"><span class="brand-dot"></span><span class="brand-name">Brivora</span></div>
</footer>

</body>
</html>
```